Signage Design Project

Busisness is a bakery and deli long time owned by the Tavel family. Want to develop a new outside sign that communicates it is a deli and a bakery but keeps the tavel name in the design.

The sign when produced will be about 10' by 3' . It is not lighted at present but could be if it were advantageous.

The name of the store is:

Tavel's Harbor Lane Bakery and Deli. The concept is to have a new,modern sign that reinforces that it is a deli and a bakery, as most people only know about the bakery side of the business
Updates

The name Tavel is just a reinforcer so the people kno it is still in the family.  The emphasis should be on the HARBOR LANE BAKERY and DELI

Target Market(s)

Small business breakfast and lunch customers

Industry/Entity Type

Bakery

Requirements
Must have
• Great impact from the road. Communicate that it is a deli and a bakery. Keep the Tavel name but need not be a major design element

```html
<!DOCTYPE html>
<html lang="en">
<head>
<meta charset="utf-8">
<title>Tavel's Harbor Lane Bakery and Deli — Sign</title>
<link rel="stylesheet" href="https://fonts.googleapis.com/css2?family=Fjalla+One&family=Gelasio:wght@700&display=swap">
<style>
  :root {
    --sign-red: #b3161f;
    --sign-red-deep: #9c1119;
    --band-maroon: #7a1219;
    --gold-light: #f6e39a;
    --gold-mid: #d9b24a;
    --gold-dark: #a97b22;
    --lettering: #ffffff;
  }
  html, body {
    margin: 0;
    padding: 0;
    width: 1200px;
    height: 359px;
    overflow: hidden;
    background: var(--sign-red);
  }
  .sign {
    display: block;
    width: 1200px;
    height: 359px;
  }
  .sign__family-name {
    font-family: "Fjalla One", "Arial Narrow", sans-serif;
    font-size: 38px;
    fill: var(--lettering);
  }
  .sign__business-type {
    font-family: "Gelasio", Georgia, serif;
    font-weight: 700;
    font-size: 176px;
    fill: var(--lettering);
  }
</style>
</head>
<body>
<svg class="sign" viewBox="0 0 1200 359" width="1200" height="359" xmlns="http://www.w3.org/2000/svg" aria-labelledby="sign-title">
  <title id="sign-title">Tavel's Harbor Lane Bakery and Deli</title>
  <defs>
    <linearGradient id="edge-red" x1="0" y1="0" x2="0" y2="1">
      <stop offset="0" stop-color="var(--sign-red)"/>
      <stop offset="1" stop-color="var(--sign-red-deep)"/>
    </linearGradient>
    <radialGradient id="gold-ornament" cx="0.5" cy="0.5" r="0.6">
      <stop offset="0" stop-color="var(--gold-light)"/>
      <stop offset="0.6" stop-color="var(--gold-mid)"/>
      <stop offset="1" stop-color="var(--gold-dark)" stop-opacity="0"/>
    </radialGradient>
    <linearGradient id="gold-rule" x1="0" y1="0" x2="1" y2="0">
      <stop offset="0" stop-color="var(--gold-mid)" stop-opacity="0"/>
      <stop offset="0.5" stop-color="var(--gold-light)"/>
      <stop offset="1" stop-color="var(--gold-mid)" stop-opacity="0"/>
    </linearGradient>
  </defs>

  <!-- top and bottom lattice edges -->
  <rect class="sign__edge sign__edge--top" x="0" y="0" width="1200" height="56" fill="url(#edge-red)" role="img" aria-label="Red diamond lattice pattern"/>
  <rect class="sign__edge sign__edge--bottom" x="0" y="300" width="1200" height="59" fill="url(#edge-red)" role="img" aria-label="Red diamond lattice pattern"/>

  <!-- central maroon band -->
  <rect class="sign__band" x="0" y="56" width="1200" height="244" fill="var(--band-maroon)"/>

  <!-- gold rules on band edges -->
  <rect class="sign__rule" x="370" y="53" width="460" height="3" fill="url(#gold-rule)"/>
  <rect class="sign__rule" x="370" y="300" width="460" height="3" fill="url(#gold-rule)"/>

  <!-- gold flourish ornaments -->
  <ellipse class="sign__ornament" cx="600" cy="28" rx="175" ry="27" fill="url(#gold-ornament)" role="img" aria-label="Gold scroll flourish ornament"/>
  <ellipse class="sign__ornament" cx="600" cy="331" rx="175" ry="27" fill="url(#gold-ornament)" role="img" aria-label="Gold scroll flourish ornament"/>

  <!-- lettering -->
  <text class="sign__family-name" x="587" y="130" text-anchor="middle">Tavel's Harbor Lane</text>
  <text class="sign__business-type" x="18" y="258" textLength="1160" lengthAdjust="spacingAndGlyphs">Bakery and Deli</text>
</svg>
</body>
</html>
```